Stationery Design Project for High End Wealth Management Firm

We need a stationery design for our high-end wealth management firm. Our clientele are affluent and our brand is built around providing investment services with world-class service.

The final concepts should provide a business card, letterhead, and envelope.

We like the idea of having text on the front and back and we MUST have black front and back business cards.
For the business card we have the following that needs to be included:
Company Logo & Tagline
Employee Name
Employee title
Employee Email
Website
2 seperate office cities, addresses, and phone numbers
Financial disclosure (small print)

Having black envelopes would be neat, but black is not a must for the envelopes.
Updates

Project Deadline Extended
Reason: To give the concept one more day of revisions.

Project Deadline Extended
Reason: To allow for more concepts and designs.

Target Market(s)

High Net Worth

Industry/Entity Type

Business

Requirements
Must have
• The following disclosure must be on the back of the card in small print:

Investment Advisory Services offered through Harrowfield Asset Partners LLC, a NFR Registered Investment Advisor. Vantory Wealth Management LLC is not affiliated with Harrowfield Asset Partners LLC.

Black business cards are also a must have.

Please utilize each of the 3 components of our logo in the design.

Please use our white background logo elements when designing our letterhead if you need them.
Nice to have
• Please use our company colors when designing. Utilize a combination of the elements of our logo that we have attached.

We are going to be printing our business cards on letterpress.

```html
<!DOCTYPE html>
<html lang="en">
<head>
<meta charset="utf-8">
<title>Vantory Wealth Management — Business Card</title>
<link href="https://fonts.googleapis.com/css2?family=Cinzel:wght@400;600&display=swap" rel="stylesheet">
<style>
  :root {
    --stage: #2b2b2d;
    --card-black: #0b0b0c;
    --gold: #d9a84a;
    --gold-light: #f3d58a;
    --gold-deep: #b07d24;
    --silver: #c9c9cc;
    --white: #f2f2f2;
  }
  * { margin: 0; padding: 0; box-sizing: border-box; }
  html, body {
    width: 1200px; height: 880px; overflow: hidden;
    background: var(--stage);
    font-family: "Cinzel", serif;
  }
  .stage {
    width: 1200px; height: 880px;
    display: flex; flex-direction: column; align-items: center; justify-content: center;
    gap: 40px;
  }
  .card {
    position: relative;
    width: 660px; height: 377px;
    background: var(--card-black);
    border-radius: 4px;
    box-shadow: 0 14px 30px rgba(0,0,0,.45);
    overflow: hidden;
  }

  /* Brand lockup */
  .brand { display: flex; align-items: center; gap: 12px; white-space: nowrap; }
  .brand-dot {
    flex: none;
    width: 40px; height: 40px; border-radius: 50%;
    background: var(--gold);
  }
  .brand-name {
    font-weight: 600; font-size: 52px; letter-spacing: 2px;
    color: var(--gold); line-height: 1;
  }
  .brand-tagline {
    font-size: 16px; letter-spacing: 2px; line-height: 1.2;
    color: var(--silver);
  }

  /* Front */
  .card-front .brand {
    position: absolute; left: 50%; top: 50%;
    transform: translate(-50%, -50%);
  }

  /* Back */
  .back-swoosh { position: absolute; inset: 0; }
  .card-back .brand { position: absolute; right: 32px; top: 34px; gap: 9px; }
  .card-back .brand-dot { width: 26px; height: 26px; }
  .card-back .brand-name { font-size: 36px; }
  .card-back .brand-tagline { font-size: 12px; letter-spacing: 1.5px; }

  .contact {
    position: absolute; left: 262px; top: 112px;
    font-size: 12px; letter-spacing: .8px; line-height: 1.55;
    color: var(--white); white-space: nowrap;
  }
  .contact .label { color: var(--gold); }

  .person { position: absolute; right: 40px; bottom: 46px; text-align: right; }
  .person-name { font-size: 22px; letter-spacing: 1.5px; color: var(--gold); }
  .person-title { font-size: 13px; letter-spacing: 1.5px; color: var(--white); margin-top: 2px; }
</style>
</head>
<body>
<main class="stage">

  <section class="card card-front" aria-label="Business card front">
    <div class="brand">
      <span class="brand-dot"></span>
      <span class="brand-name">VANTORY</span>
      <span class="brand-tagline">WEALTH<br>MANAGEMENT</span>
    </div>
  </section>

  <section class="card card-back" aria-label="Business card back">
    <svg class="back-swoosh" viewBox="0 0 660 377" preserveAspectRatio="none" aria-hidden="true">
      <defs>
        <linearGradient id="goldSweep" x1="0" y1="0" x2="1" y2="1">
          <stop offset="0" stop-color="#b07d24"/>
          <stop offset=".45" stop-color="#f3d58a"/>
          <stop offset="1" stop-color="#d9a84a"/>
        </linearGradient>
      </defs>
      <path d="M0 0 H40 C120 120 190 250 330 377 H0 Z" fill="url(#goldSweep)"/>
      <path d="M0 90 C80 130 140 210 190 377 H158 C120 230 70 160 0 125 Z" fill="#0b0b0c"/>
      <path d="M60 0 C150 120 230 260 380 377" fill="none" stroke="#d9a84a" stroke-width="2"/>
    </svg>

    <div class="brand">
      <span class="brand-dot"></span>
      <span class="brand-name">VANTORY</span>
      <span class="brand-tagline">WEALTH<br>MANAGEMENT</span>
    </div>

    <div class="contact">
      <p><span class="label">OFFICE 1</span> | OFFICE CITIES ADDRESSES</p>
      <p><span class="label">OFFICE 2</span> | OFFICE CITIES ADDRESSES</p>
      <p><span class="label">P:</span> 555 014 2730 | 555 019 6412</p>
      <p><span class="label">E:</span> DANIEL.WHITCOMBE@VANTORY.COM</p>
      <p class="label">WWW.VANTORY.COM</p>
    </div>

    <div class="person">
      <p class="person-name">DANIEL WHITCOMBE</p>
      <p class="person-title">POSITION</p>
    </div>
  </section>

</main>
</body>
</html>
```